Home Staging Company needs business card design

We're a home staging company called Brightly Settled Home Staging. We would like a business card design that includes aqua and gray. Our current logo of house within chair is fine but I find we almost always use the logo in one color. I'll upload images of front and back of our current card and our logo. Note that we have dropped "Solutions" from our company name and don't want to include it on the card.

Target Market(s)

Realtors and homeowners - people interested in selling their homes

Contact Information for Business Card

Marisol Thistlewood
Brightly Settled Home Staging
757-555-0193
www.brightlysettled.com
marisol@brightlysettled.com

Font styles to use
Serif
Script

Requirements
Must have
• My logo and contact details
• UPDATE***
• I forgot to say that the company name should be included on the front of the card somehow.

```html
<!DOCTYPE html>
<html lang="en">
<head>
<meta charset="utf-8">
<title>Brightly Settled Home Staging – Business Card</title>
<link rel="stylesheet" href="https://fonts.googleapis.com/css2?family=DM+Serif+Display&family=Open+Sans:wght@400;600&display=swap">
<style>
  :root {
    --backdrop: #3a3a3a;
    --card: #232323;
    --card-edge: #2c2c2c;
    --ink-white: #f4f4f4;
    --ink-gray: #b9b9b9;
    --front-mark: #4a4a4a;
    --aqua: #55b8c4;
    --aqua-deep: #1f9ccf;
  }
  * { box-sizing: border-box; margin: 0; padding: 0; }
  html, body { width: 799px; height: 1200px; overflow: hidden; }
  body {
    background: var(--backdrop);
    font-family: "Open Sans", Arial, sans-serif;
    display: flex;
    flex-direction: column;
    align-items: center;
    justify-content: space-around;
    padding: 60px 0;
  }
  .card {
    position: relative;
    width: 640px;
    height: 366px;
    background: var(--card);
    border: 1px solid var(--card-edge);
    border-radius: 4px;
    overflow: hidden;
    box-shadow: 0 18px 40px rgba(0,0,0,.45);
  }
  /* Front */
  .card--front {
    display: flex;
    align-items: center;
    justify-content: center;
  }
  .front-name {
    font-family: "DM Serif Display", Georgia, serif;
    font-size: 40px;
    color: var(--front-mark);
    letter-spacing: .5px;
  }
  /* Back */
  .company-name {
    position: absolute;
    left: 40px;
    top: 36px;
    font-family: "DM Serif Display", Georgia, serif;
    font-size: 30px;
    line-height: 1.1;
    color: var(--ink-white);
  }
  .person {
    position: absolute;
    left: 40px;
    top: 160px;
  }
  .person-name {
    font-size: 21px;
    font-weight: 600;
    color: var(--ink-white);
  }
  .person-title {
    font-size: 13px;
    color: var(--ink-gray);
    margin-top: 2px;
  }
  .contact-list {
    list-style: none;
    margin-top: 18px;
  }
  .contact-list li {
    display: flex;
    align-items: center;
    gap: 10px;
    font-size: 14px;
    color: var(--ink-white);
    line-height: 24px;
  }
  .contact-icon { width: 13px; height: 13px; fill: var(--aqua); flex: none; }
  .decor {
    position: absolute;
    right: -90px;
    bottom: -150px;
    width: 400px;
    height: 400px;
  }
</style>
</head>
<body>

<section class="card card--front" aria-label="Card front">
  <span class="front-name">Brightly Settled</span>
</section>

<section class="card card--back" aria-label="Card back">
  <p class="company-name">Brightly Settled<br>Home Staging</p>

  <div class="person">
    <p class="person-name">Marisol Thistlewood</p>
    <p class="person-title">Managing Director</p>
    <ul class="contact-list">
      <li>
        <svg class="contact-icon" viewBox="0 0 16 16"><path d="M3 1h3l1.5 4-2 1.3a9 9 0 0 0 4.2 4.2L11 8.5l4 1.5v3a2 2 0 0 1-2 2A13 13 0 0 1 1 3a2 2 0 0 1 2-2z"/></svg>
        757-555-0193
      </li>
      <li>
        <svg class="contact-icon" viewBox="0 0 16 16"><circle cx="8" cy="8" r="6.5" fill="none" stroke="#55b8c4" stroke-width="1.6"/><path d="M1.5 8h13M8 1.5c-3 3.5-3 9.5 0 13M8 1.5c3 3.5 3 9.5 0 13" fill="none" stroke="#55b8c4" stroke-width="1.3"/></svg>
        www.brightlysettled.com
      </li>
      <li>
        <svg class="contact-icon" viewBox="0 0 16 16"><path d="M1 3h14v10H1z"/><path d="M1 3l7 6 7-6" fill="none" stroke="#232323" stroke-width="1.4"/></svg>
        marisol@brightlysettled.com
      </li>
    </ul>
  </div>

  <svg class="decor" viewBox="0 0 400 400" role="img" aria-label="Large brand emblem area in aqua and blue">
    <defs>
      <linearGradient id="decorFill" x1="0" y1="0" x2="1" y2="1">
        <stop offset="0" stop-color="#55b8c4"/>
        <stop offset="1" stop-color="#1f9ccf"/>
      </linearGradient>
    </defs>
    <circle cx="200" cy="200" r="200" fill="url(#decorFill)"/>
  </svg>
</section>

</body>
</html>
```